Counseling Practice Business Card

I need a professional looking business card incorporating my new logo that was just completed. Card needs to incorporate my name and title, description of my specialty, my address, my phone number, my fax number, my email and my website URL. I need to be able to choose design on/with different paper colors and textures.
I do not have a lot of business card ideas so I am open to anything but I want bold,sharp, clear card without additional designs other than my logo (see attached file info). I am open to different color backgrounds or paper colors including black. I do not like traditional brackets around area codes in phone number or dashes between numbers in phone number. Am open to other ways of presenting including periods between numbers as appropriate. I do not know enough to know what I like yet but I want card to coordinate and work together with my logo. My practice emphasizes natural mental health interventions so any use of color (with background paper color or the blue and green in my logo) that elicits nature is nice. In addition to black, any natural brown or wood looking background might be desirable also. Most of the offerings so far look very similar and boring.

Target Market(s)

Potential therapy clients and other professionals

Contact Information for Business Card

Card information:
Gerald M. Whitcombe, Ph.D.
Licensed Clinical Psychologist
Integrative Health Coach
4812 Marlowe Ridge Blvd SE
Suite 310
Duluth, GA 30096
(770) 415-2983 phone
(770) 581-4096 fax
drgeraldwhitcombe@quillmarsh.net
brightfernwellness.net

Font styles to use
Serif
Sans Serif
Other font styles liked:
• anything that you think looks crisp, clear and easily readable

Requirements
Must have
• Any color used should coordinate with my logo design (see attached files).
• Card should be printed horizontally so top and bottom are longest sides of rectangle.
• Background color or paper color should complement and highlight logo. Do not like a white background. black, grey, brown or any color my logo would blend well with.
Nice to have
• I would like designer to utilize color to highlight letters/name or phone-fax-web symbols.
• Bottom edge of card could be highlighted if appropriate to an idea.
Should not have
• I would NOT want the card to have a pure white background at all.
• No clear cards.
• Cards should be oriented with long sides on bottom and top, NOT sides. DO NOT LIKE THIS THIN TALL ORIENTATION.

```html
<!DOCTYPE html>
<html lang="en">
<head>
<meta charset="utf-8">
<title>Brightfern Wellness – Business Card</title>
<link rel="stylesheet" href="https://fonts.googleapis.com/css2?family=Roboto:wght@400;500;700&display=swap">
<style>
  :root {
    --backdrop: #3a302b;
    --card: #1c1d20;
    --card-edge: #2f6fc0;
    --accent: #3d86d6;
    --text: #f2f2f2;
    --rule: #55585e;
  }
  * { margin: 0; padding: 0; box-sizing: border-box; }
  html, body {
    width: 1200px; height: 715px; overflow: hidden;
    background: var(--backdrop);
    font-family: "Roboto", Arial, sans-serif;
  }
  .stage {
    width: 1200px; height: 715px;
    display: flex; align-items: center; justify-content: center; gap: 50px;
  }
  .card {
    width: 525px; height: 300px;
    background: var(--card);
    border-bottom: 6px solid var(--card-edge);
    border-radius: 4px;
    position: relative;
    color: var(--text);
  }
  .brand {
    display: flex; align-items: center; gap: 10px;
    color: var(--accent);
    font-weight: 700; letter-spacing: 0.3px;
  }
  .brand-dot {
    width: 16px; height: 16px; border-radius: 50%;
    background: var(--accent); flex: none;
  }
  .hl { color: var(--accent); }

  /* front */
  .card-front .brand {
    position: absolute; top: 112px; left: 0; right: 0;
    justify-content: center; font-size: 30px; white-space: nowrap;
  }
  .card-front .site {
    position: absolute; bottom: 34px; left: 0; right: 0;
    text-align: center; font-size: 14px;
  }

  /* back */
  .card-back { display: flex; padding: 34px 34px 30px 26px; }
  .card-back .brand-col {
    width: 170px; flex: none;
    display: flex; align-items: center; justify-content: center;
    border-right: 1px solid var(--rule);
    margin-right: 26px;
  }
  .card-back .brand {
    flex-direction: column; text-align: center;
    font-size: 24px; line-height: 1.15;
  }
  .info-col { flex: 1; min-width: 0; }
  .person-name {
    color: var(--accent); font-weight: 700; font-size: 18px; margin-bottom: 4px;
    white-space: nowrap;
  }
  .person-title { font-size: 13px; line-height: 1.4; }
  .rule { height: 1px; background: var(--rule); margin: 14px 0 12px; }
  .rule-accent { background: var(--accent); margin: 10px 0 0; }
  .contact { font-size: 12.5px; line-height: 1.55; white-space: nowrap; }
  .contact .addr { margin-bottom: 6px; }
  .contact .label { color: var(--accent); font-weight: 500; display: inline-block; width: 22px; }
</style>
</head>
<body>
<main class="stage">
  <section class="card card-front" aria-label="Card front">
    <div class="brand"><span class="brand-dot"></span>Brightfern Wellness</div>
    <p class="site">www.<span class="hl">brightfernwellness</span>.net</p>
  </section>

  <section class="card card-back" aria-label="Card back">
    <div class="brand-col">
      <div class="brand"><span class="brand-dot"></span><span>Brightfern<br>Wellness</span></div>
    </div>
    <div class="info-col">
      <h1 class="person-name">Gerald M. Whitcombe, Ph.D.</h1>
      <p class="person-title">Licensed Clinical Psychologist<br>Integrative Health Coach</p>
      <div class="rule"></div>
      <div class="contact">
        <p class="addr">4812 Marlowe Ridge Blvd SE<br>Suite 310 Duluth, GA 30096</p>
        <p><span class="label">P :</span> 770.415.2983</p>
        <p><span class="label">F :</span> 770.581.4096</p>
        <p><span class="label">E :</span> drgeraldwhitcombe@quillmarsh.net</p>
        <p><span class="label">W :</span> www.<span class="hl">brightfernwellness</span>.net</p>
      </div>
      <div class="rule rule-accent"></div>
    </div>
  </section>
</main>
</body>
</html>
```